Business Cards Needed for Innovative Healthcare Marketing Company

We are a marketing company focused on healthcare. Our company is all about rebranding yourself renewing your image and generating results. The phoenix stands for "reborn" or "rising" which we provide new brands for our clients we take their old brands and renew it with creativity and innovation. I am looking for a business card with color dimension. I have attached an example of a card I think has the look and feel of what I am trying to accomplish. I like that the card example has black and grey font colors, I like the font placement and the small logo, I really like the use of the colors on the right those are the colors of my logo. My logo is phoenix so maybe incorporating flames similar to that design. I would like the back a solid color maybe red with an opaque version of the logo and website. As a marketing company I am always open to creative liberty!

Target Market(s)

Doctors and business professionals.

Industry/Entity Type

Marketing

Contact Information for Business Card

Valcorne Health Care Marketing
Marla Tenwick- CEO
#(512)638-2974
email-marla@valcorne.com
website- valcorne.com

Font styles to use
Sans Serif

Colors
ec1f27
f37122
ffc214
fbed22
fbf289
f04a50

Requirements
Must have
• The logo and required information
Nice to have
• icons by the information
Should not have
• child like font

```html
<!DOCTYPE html>
<html lang="en">
<head>
<meta charset="utf-8">
<title>Valcorne Health Care Marketing – Business Cards</title>
<link rel="stylesheet" href="https://fonts.googleapis.com/css2?family=Raleway:wght@300;400;600&display=swap">
<style>
  :root {
    --backdrop: #1f1f1f;
    --card: #ffffff;
    --brand-red: #b5272d;
    --brand-deep: #a3242a;
    --brand-orange: #f37122;
    --brand-amber: #f28a22;
    --text-grey: #6b6b6b;
    --rule: #d9a3a3;
  }
  * { margin: 0; padding: 0; box-sizing: border-box; }
  html, body { width: 1200px; height: 950px; overflow: hidden; }
  body {
    background: var(--backdrop);
    font-family: "Raleway", sans-serif;
    position: relative;
  }
  .card {
    position: absolute;
    left: 290px;
    width: 620px;
    height: 354px;
    background: var(--card);
    overflow: hidden;
  }
  .card--back { top: 90px; }
  .card--front { top: 506px; }

  /* brand block */
  .brand { display: flex; align-items: center; gap: 18px; }
  .brand__mark {
    width: 74px; height: 74px; border-radius: 50%;
    background: var(--brand-orange);
    flex: none;
  }
  .brand__text { color: var(--brand-red); font-weight: 300; line-height: 1; }
  .brand__name { font-size: 46px; letter-spacing: 2px; }
  .brand__tagline {
    font-size: 13px; letter-spacing: 1px;
    border-top: 1px solid var(--rule);
    margin-top: 5px; padding-top: 5px;
  }

  .card--back .brand {
    position: absolute; left: 150px; top: 112px;
  }
  .card--back .website {
    position: absolute; left: 0; right: 0; top: 246px;
    text-align: center;
    font-size: 15px; letter-spacing: 5px;
    color: var(--text-grey);
  }

  /* front */
  .emblem-area {
    position: absolute;
    left: -40px; top: 20px;
    width: 420px; height: 380px;
    border-radius: 50% 50% 0 0 / 60% 60% 0 0;
    background: linear-gradient(160deg, var(--brand-deep) 0%, #d0502a 50%, var(--brand-amber) 100%);
  }
  .card--front .brand {
    position: absolute; right: 28px; top: 26px;
  }
  .card--front .brand__name { font-size: 40px; }
  .card--front .brand__tagline { font-size: 11.5px; }

  .person {
    position: absolute; right: 28px; top: 136px;
    text-align: right;
  }
  .person__name { color: var(--brand-red); font-weight: 600; font-size: 20px; }
  .person__role { color: var(--brand-orange); font-weight: 600; font-size: 13px; margin-top: 2px; }

  .contact {
    position: absolute; right: 28px; top: 206px;
    list-style: none;
    color: var(--text-grey);
    font-size: 14px;
  }
  .contact__item {
    display: flex; justify-content: flex-end; align-items: center;
    gap: 10px; height: 24px;
  }
  .contact__icon { width: 16px; height: 16px; flex: none; }
</style>
</head>
<body>

<section class="card card--back" aria-label="Card back">
  <div class="brand">
    <span class="brand__mark" aria-hidden="true"></span>
    <div class="brand__text">
      <div class="brand__name">VALCORNE</div>
      <div class="brand__tagline">HEALTHCARE MARKETING</div>
    </div>
  </div>
  <p class="website">www.valcorne.com</p>
</section>

<section class="card card--front" aria-label="Card front">
  <div class="emblem-area" role="img" aria-label="Large rising phoenix emblem in red to orange"></div>

  <div class="brand">
    <div class="brand__text">
      <div class="brand__name">VALCORNE</div>
      <div class="brand__tagline">HEALTHCARE MARKETING</div>
    </div>
  </div>

  <div class="person">
    <div class="person__name">Marla Tenwick</div>
    <div class="person__role">CEO</div>
  </div>

  <ul class="contact">
    <li class="contact__item">(512)638-2974
      <svg class="contact__icon" viewBox="0 0 16 16" aria-hidden="true">
        <circle cx="8" cy="8" r="8" fill="#b5272d"/>
        <path d="M5.2 4.2l1.5-.4.8 1.8-1 .8a5 5 0 0 0 2.3 2.3l.8-1 1.8.8-.4 1.5c-3.2.3-6.1-2.6-5.8-5.8z" fill="#fff"/>
      </svg>
    </li>
    <li class="contact__item">marla@valcorne.com
      <svg class="contact__icon" viewBox="0 0 16 16" aria-hidden="true">
        <circle cx="8" cy="8" r="8" fill="#b5272d"/>
        <rect x="4" y="5" width="8" height="6" fill="#fff"/>
        <path d="M4 5l4 3.2L12 5" fill="none" stroke="#b5272d" stroke-width="0.9"/>
      </svg>
    </li>
    <li class="contact__item">www.valcorne.com
      <svg class="contact__icon" viewBox="0 0 16 16" aria-hidden="true">
        <circle cx="8" cy="8" r="8" fill="#b5272d"/>
        <g fill="none" stroke="#fff" stroke-width="0.9">
          <circle cx="8" cy="8" r="4"/>
          <ellipse cx="8" cy="8" rx="1.8" ry="4"/>
          <path d="M4 8h8"/>
        </g>
      </svg>
    </li>
  </ul>
</section>

</body>
</html>
```